BrivoTerna. Lantern of the Steady Harvest. Business card

Professional business card for BrivoTerna (Lantern of the Steady Harvest)
My rationale: Strategy-> Execution-> Results-> Value that lead to the BrivoTerna name: We put the Lantern of the Steady Harvest.
We deliver value to our customers helping them at defining a good strategy (cyan arrow). 90% of well formulated strategies fail due to poor execution so we also consider strategical execution very important (green arrow). Due to the execution we obtain the results (blue arrow). Finally, the results provide feedback to redefine strategy, and the new strategy has to be executed and new results obtained providing new feedback and on and on. It's like a wheel that finally, must create corporate value: value for shareholders, staholders, employees, providers...-

Target Market(s)

CEOs and steering comitees , invewrnent funds

Industry/Entity Type

Business Consultant

Contact Information for Business Card

Teodoro Vinsquel
CEO & Founder
teodoro.vinsquel@brivoterna-example.com
Mobile: +34 655.803.912
www.brivoterna-example.com

Colors

Designer to choose colors to be used in the design.

Requirements
Nice to have
• Nice to hace the words: Strategy, execution, results
• Nice to vave the claim: Lantern of the Steady Harvest
• The three colors should be shown:
• cyan for STRATEGY
• green for EXECUTION
• blue for RESULTS
Should not have
• Complete black background

```html
<!DOCTYPE html>
<html lang="en">
<head>
<meta charset="utf-8">
<title>BrivoTerna – Business Card</title>
<link href="https://fonts.googleapis.com/css2?family=Source+Sans+3:wght@400;600;700&display=swap" rel="stylesheet">
<style>
  :root {
    --page-bg: #e0e0e0;
    --card-bg: #fbfbfb;
    --brand-blue: #003399;
    --brand-green: #8dc63f;
    --brand-cyan: #00aeef;
    --text-dark: #333333;
    --white: #ffffff;
  }
  * { box-sizing: border-box; margin: 0; padding: 0; }
  html, body {
    width: 1130px;
    height: 1200px;
    overflow: hidden;
    background: var(--page-bg);
    font-family: "Source Sans 3", sans-serif;
  }
  .card {
    position: absolute;
    left: 324px;
    top: 182px;
    width: 480px;
    height: 839px;
    background: var(--card-bg);
    border-radius: 240px 240px 24px 24px / 240px 240px 24px 24px;
    overflow: hidden;
  }
  .brand-mark {
    position: absolute;
    left: 186px;
    top: 140px;
    width: 108px;
    height: 108px;
    border-radius: 50%;
    background: var(--brand-blue);
  }
  .brand-name {
    position: absolute;
    left: 0;
    top: 278px;
    width: 100%;
    text-align: center;
    font-size: 78px;
    font-weight: 700;
    letter-spacing: -2px;
    color: var(--brand-blue);
    line-height: 1;
  }
  .name-band {
    position: absolute;
    left: 0;
    top: 424px;
    width: 100%;
    height: 85px;
    border-top: 4px solid var(--brand-green);
    background: var(--brand-blue);
    color: var(--white);
    text-align: center;
  }
  .person-name {
    margin-top: 8px;
    font-size: 31px;
    font-weight: 700;
    line-height: 1.1;
  }
  .person-role {
    font-size: 21px;
    font-weight: 400;
    line-height: 1.3;
  }
  .contact-icons {
    position: absolute;
    left: 0;
    top: 568px;
    width: 100%;
    display: flex;
    justify-content: center;
    gap: 12px;
  }
  .contact-icons svg {
    width: 35px;
    height: 35px;
    display: block;
  }
  .contact-list {
    position: absolute;
    left: 0;
    top: 618px;
    width: 100%;
    text-align: center;
    list-style: none;
    font-size: 21px;
    line-height: 32px;
    color: var(--text-dark);
  }
  .tagline {
    position: absolute;
    left: 0;
    top: 780px;
    width: 100%;
    text-align: center;
    font-size: 22px;
    font-weight: 700;
    letter-spacing: 1.2px;
    color: var(--brand-cyan);
  }
  .tagline .dot { margin: 0 8px; }
</style>
</head>
<body>
  <main class="card">
    <div class="brand-mark"></div>
    <h1 class="brand-name">BrivoTerna</h1>

    <section class="name-band">
      <p class="person-name">Teodoro Vinsquel</p>
      <p class="person-role">CEO &amp; Founder</p>
    </section>

    <div class="contact-icons">
      <svg viewBox="0 0 36 36" aria-label="Mobile">
        <circle cx="18" cy="18" r="18" fill="var(--brand-blue)"/>
        <rect x="12.5" y="8" width="11" height="20" rx="2" fill="none" stroke="#fff" stroke-width="1.8"/>
        <line x1="12.5" y1="11.5" x2="23.5" y2="11.5" stroke="#fff" stroke-width="1.2"/>
        <line x1="12.5" y1="24" x2="23.5" y2="24" stroke="#fff" stroke-width="1.2"/>
        <circle cx="18" cy="26" r="0.9" fill="#fff"/>
      </svg>
      <svg viewBox="0 0 36 36" aria-label="Email">
        <circle cx="18" cy="18" r="18" fill="var(--brand-blue)"/>
        <rect x="8.5" y="11" width="19" height="14" fill="#fff"/>
        <path d="M8.5 11 L18 19 L27.5 11 M8.5 25 L15 18.5 M27.5 25 L21 18.5" fill="none" stroke="var(--brand-blue)" stroke-width="1.4"/>
      </svg>
      <svg viewBox="0 0 36 36" aria-label="Website">
        <circle cx="18" cy="18" r="18" fill="var(--brand-blue)"/>
        <g fill="none" stroke="#fff" stroke-width="1.4">
          <circle cx="18" cy="18" r="9.5"/>
          <ellipse cx="18" cy="18" rx="4.2" ry="9.5"/>
          <line x1="18" y1="8.5" x2="18" y2="27.5"/>
          <line x1="8.5" y1="18" x2="27.5" y2="18"/>
          <path d="M10 13 H26 M10 23 H26"/>
        </g>
      </svg>
    </div>

    <ul class="contact-list">
      <li>+34 655.803.912</li>
      <li>teodoro.vinsquel@brivoterna-example.com</li>
      <li>www.brivoterna-example.com</li>
    </ul>

    <p class="tagline">RESULTS<span class="dot">•</span>EXECUTION<span class="dot">•</span>STRATEGY</p>
  </main>
</body>
</html>
```